plumbers buisness card

A buisness card for a plumbing buisness
needs to have a water theme with navy blue, light blue and white
with an image of either a water drop, pipes, tools or something relating to plumbing and incorperating my buisness name as a logo

"Kettering Plumbing" is the words that need to stand out with "& gasfitting" to be smaller

spelling error on brief, "maintenance"
and also could you include my email d_kettering@mailwave.com.au

Industry/Entity Type

Plumbing

Contact Information for Business Card

Kettering Plumbing & Gasfitting

declan kettering
0432961085

specialising in
-new homes
-maitenance
-renovations

license no.
-73840

```html
<!DOCTYPE html>
<html lang="en">
<head>
<meta charset="utf-8">
<title>Kettering Plumbing &amp; Gasfitting – Business Card</title>
<link rel="stylesheet" href="https://fonts.googleapis.com/css2?family=Roboto+Condensed:wght@700&family=Source+Sans+3:wght@400;600;700&display=swap">
<style>
  :root {
    --stage: #33302d;
    --card-white: #ffffff;
    --brand-blue: #4a56b3;
    --text-dark: #3a3a3a;
    --label-white: #ffffff;
    --chrome-highlight: #f3f5f7;
    --chrome-light: #dde1e5;
    --chrome-mid: #aeb4bb;
    --chrome-dark: #7d848c;
  }
  * { box-sizing: border-box; margin: 0; padding: 0; }
  html, body { width: 1200px; height: 426px; overflow: hidden; background: var(--stage); }
  .canvas { position: relative; width: 1200px; height: 426px; background: var(--stage); }

  .side-label {
    position: absolute; top: 26px;
    font-family: "Source Sans 3", Arial, sans-serif;
    font-size: 38px; font-weight: 400; color: var(--label-white);
    transform: translateX(-50%); line-height: 1;
  }
  .side-label--front { left: 320px; }
  .side-label--back { left: 893px; }

  .card { position: absolute; top: 87px; width: 535px; height: 305px; background: var(--card-white); overflow: hidden; }
  .card--front { left: 50px; }
  .card--back { left: 617px; }

  /* Front */
  .product-photo--tap {
    position: absolute; left: 14px; top: 14px; width: 146px; height: 277px;
    border-radius: 6px;
    background: linear-gradient(100deg, var(--chrome-light) 0%, var(--chrome-highlight) 30%, var(--chrome-mid) 62%, var(--chrome-dark) 100%);
  }
  .accent-stripe { position: absolute; top: 0; left: 173px; width: 6px; height: 305px; background: var(--brand-blue); }
  .brand-panel {
    position: absolute; top: 0; left: 186px; right: 0; height: 305px;
    background: var(--brand-blue); color: var(--card-white);
    font-family: "Roboto Condensed", "Arial Narrow", sans-serif; font-weight: 700;
    text-align: center;
  }
  .contact-name { position: absolute; top: 25px; left: 0; right: 0; font-family: "Roboto Condensed", "Arial Narrow", sans-serif; font-size: 21px; font-weight: 700; line-height: 1; }
  .contact-phone { position: absolute; top: 52px; left: 0; right: 0; font-family: "Roboto Condensed", "Arial Narrow", sans-serif; font-size: 19px; font-weight: 700; line-height: 1; }
  .brand-name { position: absolute; top: 106px; left: 0; right: 0; font-size: 43px; line-height: 1; letter-spacing: 0.5px; }
  .brand-trade { position: absolute; top: 159px; left: 0; right: 0; font-size: 35px; line-height: 1; }
  .brand-amp { position: absolute; top: 209px; left: 0; right: 0; font-size: 22px; line-height: 1; }
  .brand-secondary { position: absolute; top: 245px; left: 0; right: 0; font-size: 27px; line-height: 1; }

  /* Back */
  .product-photo--mixer {
    position: absolute; left: 10px; top: 22px; width: 205px; height: 262px;
    border-radius: 6px;
    background: linear-gradient(160deg, var(--chrome-highlight) 0%, var(--chrome-light) 40%, var(--chrome-mid) 75%, var(--chrome-dark) 100%);
  }
  .services {
    position: absolute; left: 318px; width: 144px; top: 79px;
    font-family: "Source Sans 3", Arial, sans-serif; color: var(--text-dark);
    text-align: center; white-space: nowrap;
  }
  .services-heading {
    display: inline-block; font-size: 16px; font-weight: 700; color: var(--brand-blue);
    border-bottom: 2px solid var(--brand-blue); padding-bottom: 1px; line-height: 1.1;
  }
  .services-list { list-style: none; margin-top: 14px; font-size: 15px; line-height: 19.5px; }
  .card-details { position: absolute; left: 250px; width: 280px; top: 188px; text-align: center; font-family: "Source Sans 3", Arial, sans-serif; color: var(--text-dark); font-size: 14.5px; line-height: 18.5px; }
</style>
</head>
<body>
<main class="canvas">
  <h2 class="side-label side-label--front">Front</h2>
  <h2 class="side-label side-label--back">Back</h2>

  <section class="card card--front">
    <div class="product-photo--tap" role="img" aria-label="Photo of a chrome sensor basin tap"></div>
    <div class="accent-stripe"></div>
    <div class="brand-panel">
      <p class="contact-name">Declan Kettering</p>
      <p class="contact-phone">0432961085</p>
      <p class="brand-name">KETTERING</p>
      <p class="brand-trade">Plumbing</p>
      <p class="brand-amp">&amp;</p>
      <p class="brand-secondary">gasfitting</p>
    </div>
  </section>

  <section class="card card--back">
    <div class="product-photo--mixer" role="img" aria-label="Photo of a chrome single-lever basin mixer with drain plug"></div>
    <div class="services">
      <span class="services-heading">Specialising in :</span>
      <ul class="services-list">
        <li>new homes</li>
        <li>maintenance</li>
        <li>renovations</li>
      </ul>
    </div>
    <div class="card-details">
      <p>e-mail :&nbsp; d_kettering@mailwave.com.au</p>
      <p>license no. 73840</p>
    </div>
  </section>
</main>
</body>
</html>
```